Road Construction Company needs business cards

We would like a new business card designed for our business.

We're a road construction company based in Qld, Australia.

Can the business card please have the following information on it.

Name: Warren Halbeck
Position: General Manager
Phone: 0472 915 348
Email: Warren.halbeck@tovrin.com.au
Address: 87 Marrow Ave, Pendlebay, QLD, 4023
Website: www.tovrin.com.au

Visually we'd like the card to be professional and simple.

Attached is our logo.

Our website is www.tovrin.com.au

Target Market(s)

Men aged 25-60

Contact Information for Business Card

As listed in project description

Font styles to use
Serif

Requirements
Must have
• Large logo on back of card

```html
<!DOCTYPE html>
<html lang="en">
<head>
<meta charset="utf-8">
<title>Tovrin Business Card</title>
<link rel="stylesheet" href="https://fonts.googleapis.com/css2?family=Open+Sans:wght@400;600;700&display=swap">
<style>
  :root {
    --backdrop: #2b2f36;
    --card: #ffffff;
    --brand-blue: #1457a8;
    --band-blue: #2f88cf;
    --ink: #111418;
    --rule: #2a2a2a;
    --band-text: #ffffff;
  }
  * { box-sizing: border-box; margin: 0; padding: 0; }
  html, body { width: 1200px; height: 780px; overflow: hidden; }
  body {
    background: var(--backdrop);
    font-family: "Open Sans", Arial, sans-serif;
    position: relative;
  }
  .card {
    position: absolute;
    top: 235px;
    width: 540px;
    height: 310px;
    background: var(--card);
    border-radius: 22px;
    overflow: hidden;
  }
  .card--front { left: 30px; }
  .card--back { left: 630px; }

  .brand-name {
    font-family: "Open Sans", Arial, sans-serif;
    font-weight: 700;
    color: var(--brand-blue);
    letter-spacing: 2px;
    line-height: 1;
  }
  .card--front .brand-name {
    position: absolute;
    left: 36px;
    top: 66px;
    font-size: 44px;
  }
  .card--back .brand-name {
    position: absolute;
    inset: 0;
    display: flex;
    align-items: center;
    justify-content: center;
    font-size: 92px;
    letter-spacing: 4px;
  }

  .divider {
    position: absolute;
    left: 0; top: 0;
    width: 540px; height: 310px;
  }

  .contact {
    position: absolute;
    left: 298px;
    top: 70px;
    color: var(--ink);
  }
  .contact__name {
    font-weight: 600;
    font-size: 27px;
    color: var(--brand-blue);
    line-height: 1.1;
  }
  .contact__role {
    font-size: 14px;
    margin-top: 2px;
  }
  .contact__list {
    list-style: none;
    margin-top: 14px;
    font-size: 13.5px;
    line-height: 1.75;
  }
  .contact__list li {
    display: flex;
    align-items: center;
    gap: 8px;
  }
  .contact__list svg { width: 13px; height: 13px; flex: none; }

  .address-band {
    position: absolute;
    left: 0; bottom: 0;
    width: 100%;
    height: 46px;
    background: var(--band-blue);
    color: var(--band-text);
    font-size: 15px;
    display: flex;
    align-items: center;
    padding-left: 36px;
  }
</style>
</head>
<body>
  <section class="card card--front" aria-label="Business card front">
    <div class="brand-name">TOVRIN</div>

    <svg class="divider" viewBox="0 0 540 310" aria-hidden="true">
      <line x1="300" y1="30" x2="250" y2="240" stroke="var(--rule)" stroke-width="1"/>
    </svg>

    <div class="contact">
      <h1 class="contact__name">Warren Halbeck</h1>
      <p class="contact__role">General Manager</p>
      <ul class="contact__list">
        <li>
          <svg viewBox="0 0 16 16" aria-hidden="true"><path d="M4 1.5l2.2 2.6-1.3 1.6a9 9 0 0 0 5.4 5.4l1.6-1.3 2.6 2.2-1.4 2.4C7 14 2 9 1.6 2.9z" fill="var(--band-blue)"/></svg>
          <span>0472 915 348</span>
        </li>
        <li>
          <svg viewBox="0 0 16 16" aria-hidden="true"><circle cx="8" cy="8" r="6.5" fill="none" stroke="var(--band-blue)" stroke-width="1.5"/><path d="M1.5 8h13M8 1.5c-3 3.5-3 9.5 0 13M8 1.5c3 3.5 3 9.5 0 13" fill="none" stroke="var(--band-blue)" stroke-width="1.2"/></svg>
          <span>www.tovrin.com.au</span>
        </li>
        <li>
          <svg viewBox="0 0 16 16" aria-hidden="true"><rect x="1.5" y="3.5" width="13" height="9" rx="1" fill="none" stroke="var(--band-blue)" stroke-width="1.5"/><path d="M1.5 4l6.5 5 6.5-5" fill="none" stroke="var(--band-blue)" stroke-width="1.3"/></svg>
          <span>Warren.halbeck@tovrin.com.au</span>
        </li>
      </ul>
    </div>

    <div class="address-band">87 Marrow Ave, Pendlebay, QLD, 4023</div>
  </section>

  <section class="card card--back" aria-label="Business card back">
    <div class="brand-name">TOVRIN</div>
  </section>
</body>
</html>
```